Water ATM Card

Need a design for water ATM cards. Size of card is 3.375 x 2.125 inch
On the Front include the Cedar hollow Logo.
Bottom right corner should have Price $100
On the Back
This card is to be used to access water refills at any Cedar Hollow Water Vending Machines.
Please contact (869) 418 2930 or (869) 534 1276 or email clearflowbox@mailvista.example for any assistance or recharging of card.

```html
<!DOCTYPE html>
<html lang="en">
<head>
<meta charset="utf-8">
<title>Cedar Hollow Water Card</title>
<link href="https://fonts.googleapis.com/css2?family=Montserrat:wght@400;500;700&display=swap" rel="stylesheet">
<style>
  :root {
    --backdrop: #9b9b9b;
    --card-white: #ffffff;
    --brand-blue: #2a5aa5;
    --brand-sky: #2a7fc1;
    --ink: #1d1d1f;
    --price-green: #2e9e48;
    --band-dark: #263a87;
    --band-light: #1f63aa;
    --back-top: #2f80c2;
    --back-mid: #3a5aa2;
    --back-bottom: #2b3987;
    --back-brand: #8ea9e0;
  }
  * { box-sizing: border-box; margin: 0; padding: 0; }
  html, body { width: 1093px; height: 1200px; overflow: hidden; }
  body {
    background: var(--backdrop);
    font-family: "Montserrat", Arial, sans-serif;
    position: relative;
  }
  .card {
    position: absolute;
    left: 264px;
    width: 581px;
    height: 364px;
    overflow: hidden;
  }
  .card--front { top: 225px; background: var(--card-white); }
  .card--back { top: 616px; }

  .brand-name {
    position: absolute;
    font-weight: 700;
    color: var(--brand-sky);
    letter-spacing: 0.5px;
    white-space: nowrap;
    display: flex;
    align-items: center;
    gap: 8px;
  }
  .brand-name .brand-dot {
    width: 12px; height: 12px; border-radius: 50%;
    background: var(--brand-sky);
  }
  .card--front .brand-name { left: 52px; top: 200px; font-size: 22px; }

  .divider {
    position: absolute;
    left: 281px; top: 126px;
    width: 1.5px; height: 146px;
    background: var(--brand-blue);
  }
  .holder-name {
    position: absolute; left: 292px; top: 122px;
    font-size: 19px; font-weight: 700; color: var(--brand-blue);
    letter-spacing: 0.3px;
  }
  .holder-role {
    position: absolute; left: 292px; top: 151px;
    font-size: 12.5px; font-weight: 400; color: var(--ink);
  }
  .contact-list {
    position: absolute; left: 292px; top: 187px;
    list-style: none;
  }
  .contact-list li {
    display: flex; align-items: center; gap: 6px;
    font-size: 13px; color: var(--ink);
    height: 22px;
  }
  .contact-list li.phone-row { height: 26px; }
  .contact-list svg { width: 12px; height: 12px; flex: none; fill: var(--brand-blue); }
  .price {
    position: absolute; right: 38px; top: 309px;
    font-size: 18px; font-weight: 700; color: var(--price-green);
  }
  .base-band {
    position: absolute; left: 0; bottom: 0; width: 100%; height: 14px;
    background: linear-gradient(100deg, var(--band-dark) 0%, var(--band-dark) 42%, #2c86c9 50%, var(--band-light) 58%, var(--band-light) 100%);
  }

  .back-field {
    position: absolute; inset: 0;
    background: linear-gradient(160deg, var(--back-top) 0%, var(--back-mid) 50%, var(--back-bottom) 100%);
  }
  .card--back .brand-name {
    left: 0; right: 0; top: 196px; justify-content: center;
    font-size: 26px; color: var(--back-brand);
  }
  .card--back .brand-name .brand-dot { background: var(--back-brand); width: 14px; height: 14px; }
  .back-note {
    position: absolute; left: 50px; right: 50px; top: 252px;
    text-align: center; font-size: 11.5px; line-height: 1.5; color: #ffffff;
  }
  .back-note .note-end { display: block; font-size: 13px; margin-top: 4px; }
</style>
</head>
<body>
  <section class="card card--front">
    <div class="brand-name"><span class="brand-dot"></span>CEDAR HOLLOW</div>
    <div class="divider"></div>
    <h1 class="holder-name">DANA WHITLOCK</h1>
    <p class="holder-role">OWER</p>
    <ul class="contact-list">
      <li class="phone-row">
        <svg viewBox="0 0 24 24"><path d="M6.6 10.8a15.1 15.1 0 0 0 6.6 6.6l2.2-2.2a1 1 0 0 1 1-.25 11.4 11.4 0 0 0 3.6.57 1 1 0 0 1 1 1V20a1 1 0 0 1-1 1A17 17 0 0 1 3 4a1 1 0 0 1 1-1h3.5a1 1 0 0 1 1 1c0 1.25.2 2.45.57 3.57a1 1 0 0 1-.25 1z"/></svg>
        (869) 418 2930
      </li>
      <li class="phone-row">
        <svg viewBox="0 0 24 24"><path d="M7 1h10a2 2 0 0 1 2 2v18a2 2 0 0 1-2 2H7a2 2 0 0 1-2-2V3a2 2 0 0 1 2-2zm0 3v14h10V4zm5 15.5a1.2 1.2 0 1 0 0 2.4 1.2 1.2 0 0 0 0-2.4z"/></svg>
        (869) 534 1276
      </li>
      <li>
        <svg viewBox="0 0 24 24"><path d="M2 5h20v14H2zm2 2v.4l8 5 8-5V7zm0 2.8V17h16V9.8l-8 5z"/></svg>
        clearflowbox@mailvista.example
      </li>
      <li>
        <svg viewBox="0 0 24 24"><path d="M12 2a10 10 0 1 0 0 20 10 10 0 0 0 0-20zm-1 17.9A8 8 0 0 1 4.1 10.1L9 15v1a2 2 0 0 0 2 2zm6.9-2.5A2 2 0 0 0 16 16h-1v-3a1 1 0 0 0-1-1H8v-2h2a1 1 0 0 0 1-1V7h2a2 2 0 0 0 2-2v-.4a8 8 0 0 1 2.9 12.8z"/></svg>
        www.cedarhollowwater.example
      </li>
    </ul>
    <p class="price">Price $100</p>
    <div class="base-band"></div>
  </section>

  <section class="card card--back">
    <div class="back-field" role="img" aria-label="Blue gradient field with a repeating faint mountain and wave pattern"></div>
    <div class="brand-name"><span class="brand-dot"></span>CEDAR HOLLOW</div>
    <p class="back-note">
      This card is to be used to access water refills at any Cedar Hollow Water Vending Machines.
      Please contact (869) 418 2930 or (869) 534 1276 or email clearflowbox@mailvista.example
      <span class="note-end">for any assistance or recharging of card.</span>
    </p>
  </section>
</body>
</html>
```